KAJU Freightways #ALLKAJU Business Cards & Letterhead

I am looking to business cards designed for our organization. We are currently undergoing a small re-branding that is taking place. Our organization is called KAJU Freightways and we are headquartered in Phoenix, AZ. We primarily provide transportation and logistics services to the Marlow Parcel Bureau who is our largest customer. I would like to see a design that incorporates name, title, contact info, website, and address (this will be different depending on the employee). I would also like to see some color on the business card using our logo colors or a variation. I would like our logo on the back of the business card with the website displayed. The final design should communicate that we are a next generation transportation operate that focuses on being driver-first, customer-centric, innovative, and sustainable.We would also like our #ALLKAJU catch phrase incorporated as well.

Target Market(s)

Transportation & Logistics

Industry/Entity Type

Trucking Company

Contact Information for Business Card

-First and Last Name
-Position Title
-Contact Phone
-Contact Email
-Physical Address

Font styles to use
Serif

Colors

Designer to choose colors to be used in the design.

Requirements
Must have
• -KAJU logo prominently displayed
• -#ALLKAJU catch phrase used
• -Some amount of color, design gradient, etc.
• -Logo on the back with website listed (https://www.kajufreightco.example)

```html
<!DOCTYPE html>
<html lang="en">
<head>
<meta charset="utf-8">
<title>KAJU Freightways Business Cards</title>
<link rel="stylesheet" href="https://fonts.googleapis.com/css2?family=Roboto+Serif:opsz,wght@8..144,400;8..144,600;8..144,700&display=swap">
<style>
  :root {
    --backdrop: #b4b4b4;
    --card: #f1f1f0;
    --navy: #0f3440;
    --green: #6eac2a;
    --ink: #1c3a44;
  }
  * { margin: 0; padding: 0; box-sizing: border-box; }
  html, body { width: 1200px; height: 576px; overflow: hidden; }
  body { background: var(--backdrop); position: relative; font-family: "Roboto Serif", serif; }

  .card {
    position: absolute; top: 139px; width: 485px; height: 292px;
    background: var(--card); border-radius: 10px; overflow: hidden;
  }
  .card--back { left: 82px; }
  .card--front { left: 602px; }

  .wordmark {
    position: absolute; display: flex; align-items: center; gap: 10px;
    transform: translate(-50%, -50%);
  }
  .wordmark__name {
    font-weight: 700; color: var(--navy);
    font-size: 46px; letter-spacing: 1px; line-height: 1;
  }
  .wordmark__dot { width: 12px; height: 12px; border-radius: 50%; background: var(--green); flex: none; }
  .card--back .wordmark { left: 242px; top: 132px; }
  .card--front .wordmark { left: 130px; top: 144px; }

  .tagline {
    position: absolute; left: 0; right: 0; top: 176px; text-align: center;
    font-size: 14px; font-weight: 600; letter-spacing: 3px; color: var(--green);
  }

  .back-site {
    position: absolute; left: 0; right: 0; top: 248px;
    display: flex; align-items: center; justify-content: center; gap: 18px;
  }
  .back-site__url { font-size: 12.5px; letter-spacing: 2.2px; color: var(--ink); }
  .back-site__dash { width: 42px; height: 3px; }

  .brand-band { position: absolute; left: 0; bottom: 0; width: 100%; height: 13px; display: flex; }
  .brand-band__navy { flex: 1; background: var(--navy); }
  .brand-band__green { flex: 1; background: var(--green); }

  .contact { position: absolute; left: 260px; top: 54px; color: var(--ink); }
  .contact__name { font-weight: 700; font-size: 20px; color: var(--navy); line-height: 1.1; }
  .contact__title { font-size: 12.5px; margin-top: 6px; }
  .contact__rule { width: 94px; height: 1.5px; background: var(--green); margin-top: 4px; }
  .contact__list { list-style: none; margin-top: 17px; }
  .contact__item { display: flex; align-items: center; gap: 12px; font-size: 12.5px; height: 18.5px; white-space: nowrap; }
  .contact__icon { width: 12px; height: 12px; fill: var(--green); flex: none; }
  .contact__company { font-size: 12.5px; font-weight: 700; color: var(--green); margin-top: 6px; white-space: nowrap; }
  .contact__address { font-size: 12.5px; line-height: 18px; margin-top: 2px; }
</style>
</head>
<body>

  <section class="card card--back">
    <div class="wordmark"><span class="wordmark__name">KAJU</span><span class="wordmark__dot"></span></div>
    <p class="tagline">#ALLKAJU</p>
    <div class="back-site">
      <svg class="back-site__dash" viewBox="0 0 42 3"><polygon points="0,1.5 42,0 42,3" fill="var(--green)"/></svg>
      <span class="back-site__url">www.kajufreightco.example</span>
      <svg class="back-site__dash" viewBox="0 0 42 3"><polygon points="0,0 42,1.5 0,3" fill="var(--green)"/></svg>
    </div>
    <div class="brand-band"><span class="brand-band__navy"></span><span class="brand-band__green"></span></div>
  </section>

  <section class="card card--front">
    <div class="wordmark"><span class="wordmark__name">KAJU</span><span class="wordmark__dot"></span></div>
    <div class="contact">
      <p class="contact__name">Dana Whitlock</p>
      <p class="contact__title">Chairman &amp; CEO</p>
      <div class="contact__rule"></div>
      <ul class="contact__list">
        <li class="contact__item">
          <svg class="contact__icon" viewBox="0 0 12 12"><path d="M1 4 Q6 0 11 4 L9.5 5.5 L8 4.5 L8 3.5 Q6 3 4 3.5 L4 4.5 L2.5 5.5 Z M2.5 6.5 L9.5 6.5 L10.5 11 L1.5 11 Z"/></svg>
          480-555-0142
        </li>
        <li class="contact__item">
          <svg class="contact__icon" viewBox="0 0 12 12"><path d="M1 2.5 H11 V9.5 H1 Z M1.8 3.2 L6 6.5 L10.2 3.2" stroke="var(--card)" stroke-width="0.9"/></svg>
          dana@kajufreightco.example
        </li>
        <li class="contact__item">
          <svg class="contact__icon" viewBox="0 0 12 12"><circle cx="6" cy="6" r="5"/><path d="M1 6 H11 M6 1 Q3 6 6 11 M6 1 Q9 6 6 11" stroke="var(--card)" stroke-width="0.8" fill="none"/></svg>
          www.kajufreightco.example
        </li>
      </ul>
      <p class="contact__company">KAJU Freightways &amp; Energy</p>
      <p class="contact__address">1460 North Saguaro Ridge<br>Road Phoenix, AZ 85027</p>
    </div>
  </section>

</body>
</html>
```